Brivolt Technologies business card design

We need a business card designed with our new logo. it would be great if the card could communicate it is a technology based company.

Target Market(s)

system integrators

Industry/Entity Type

technology, IOT

Contact Information for Business Card

Name, designation, Address, telephone number, email address

Requirements
Must have
• logo and company name
Nice to have
• something to do with technology

```html
<!DOCTYPE html>
<html lang="en">
<head>
<meta charset="utf-8">
<title>Brivolt Technologies – Business Card</title>
<link rel="stylesheet" href="https://fonts.googleapis.com/css2?family=Arimo:wght@400;700&display=swap">
<style>
  :root {
    --bg: #979797;
    --card-light: #ffffff;
    --card-dark: #393939;
    --ink: #2b2b2b;
    --brand-dark: #333333;
    --accent: #f39221;
    --watermark: #f4f4f4;
  }
  * { box-sizing: border-box; margin: 0; padding: 0; }
  html, body { width: 1200px; height: 1059px; overflow: hidden; }
  body {
    position: relative;
    background: var(--bg);
    font-family: "Arimo", Arial, sans-serif;
    color: var(--ink);
  }
  .card {
    position: absolute;
    border-radius: 24px;
    overflow: hidden;
  }
  .card-front { left: 256px; top: 89px; width: 688px; height: 390px; background: var(--card-light); }
  .card-back { left: 253px; top: 570px; width: 694px; height: 393px; background: var(--card-dark); }

  .watermark-shape {
    position: absolute;
    left: 400px;
    top: 110px;
    width: 330px;
    height: 330px;
    background: var(--watermark);
  }

  .wordmark { position: absolute; display: flex; align-items: center; }
  .wordmark .mark-square { background: var(--accent); flex: none; }
  .wordmark .name-block { display: flex; flex-direction: column; line-height: 1; font-weight: 700; }
  .wordmark .name-main { letter-spacing: 1px; }
  .wordmark .name-sub { letter-spacing: 0.5em; }

  .card-front .wordmark { left: 31px; top: 74px; gap: 44px; color: var(--brand-dark); }
  .card-front .mark-square { width: 60px; height: 60px; }
  .card-front .name-main { font-size: 49px; }
  .card-front .name-sub { font-size: 17px; margin-top: 6px; }

  .card-back .wordmark { left: 117px; top: 141px; gap: 36px; color: var(--accent); }
  .card-back .mark-square { width: 80px; height: 80px; }
  .card-back .name-main { font-size: 70px; }
  .card-back .name-sub { font-size: 24px; margin-top: 10px; }

  .person { position: absolute; right: 30px; top: 168px; text-align: right; }
  .person-name { color: var(--accent); font-weight: 700; font-size: 27px; line-height: 1; }
  .person-role { font-size: 18px; margin-top: 8px; }

  .address { position: absolute; left: 31px; top: 226px; font-size: 18px; line-height: 21px; font-style: normal; }

  .contacts { position: absolute; left: 31px; top: 284px; list-style: none; font-size: 18px; }
  .contacts li { display: flex; align-items: center; gap: 5px; height: 27px; }
  .contacts svg { width: 13px; height: 13px; fill: var(--accent); flex: none; }
</style>
</head>
<body>
  <section class="card card-front" aria-label="Card front">
    <div class="watermark-shape" aria-hidden="true"></div>

    <div class="wordmark">
      <span class="mark-square"></span>
      <div class="name-block">
        <span class="name-main">BRIVOLT</span>
        <span class="name-sub">TECHNOLOGIES</span>
      </div>
    </div>

    <div class="person">
      <p class="person-name">DANIEL HARTMANN</p>
      <p class="person-role">CEO/Founder</p>
    </div>

    <address class="address">2280 Harbor Lane<br>Riverton AB 4519</address>

    <ul class="contacts">
      <li>
        <svg viewBox="0 0 24 24" aria-hidden="true"><path d="M6.6 10.8a15 15 0 0 0 6.6 6.6l2.2-2.2c.3-.3.7-.4 1-.2 1.1.4 2.3.6 3.6.6.6 0 1 .4 1 1V20c0 .6-.4 1-1 1A17 17 0 0 1 3 4c0-.6.4-1 1-1h3.5c.6 0 1 .4 1 1 0 1.3.2 2.5.6 3.6.1.3 0 .7-.2 1z"/></svg>
        (555) 418-3720
      </li>
      <li>
        <svg viewBox="0 0 24 24" aria-hidden="true"><path d="M2 5h20v2l-10 6L2 7z M2 9l10 6 10-6v10H2z"/></svg>
        info@brivolttechnologies.com
      </li>
      <li>
        <svg viewBox="0 0 24 24" aria-hidden="true"><path d="M12 2a10 10 0 1 0 0 20 10 10 0 0 0 0-20zm6.9 9h-3a15 15 0 0 0-1.3-6.3A8 8 0 0 1 18.9 11zM12 4c.9 1.2 1.8 3.6 1.9 7h-3.8c.1-3.4 1-5.8 1.9-7zM9.4 4.7A15 15 0 0 0 8.1 11h-3a8 8 0 0 1 4.3-6.3zM5.1 13h3a15 15 0 0 0 1.3 6.3A8 8 0 0 1 5.1 13zm6.9 7c-.9-1.2-1.8-3.6-1.9-7h3.8c-.1 3.4-1 5.8-1.9 7zm2.6-.7a15 15 0 0 0 1.3-6.3h3a8 8 0 0 1-4.3 6.3z"/></svg>
        www.brivolttechnologies.com
      </li>
    </ul>
  </section>

  <section class="card card-back" aria-label="Card back">
    <div class="wordmark">
      <span class="mark-square"></span>
      <div class="name-block">
        <span class="name-main">BRIVOLT</span>
        <span class="name-sub">TECHNOLOGIES</span>
      </div>
    </div>
  </section>
</body>
</html>
```